Natural Light/Organic/Documentary Photography Business

I like a simple, approachable, feminine, earthy/organic feel. Earth/neutral tones, nothing too loud or obnoxious. I like the watercolor look. I don't want anything too trendy or something I'll get tired of after a couple months. As far as colors, I am much more a fan of cream/taupe/blue/green...not a fan of pink or purple at all.

Target Market(s)

Weddings & Families

Industry/Entity Type

Wedding Photography

Contact Information for Business Card

website, email, phone number

Font styles to use
Other font styles liked:
• Horizontes, Gotham

Colors

Designer to choose colors to be used in the design.

Requirements
Must have
• Website: www.mirelhatchway.com
• Phone: 418.629.5073
• Email: mirel@mirelhatchway.com
Nice to have
• I like the watercolor look but its not necessary. I like simple/earthy tones. Nothing too loud or distracting. Simple & feminine without being too girly. I like an approachable/soft feel.
• Instagram: www.instagram.com/mirelhatchwayphotography/
Should not have
• NO loud colors or design or pattern. I do not want a photo of a camera or lens or anything cheesy like that.

```html
<!DOCTYPE html>
<html lang="en">
<head>
<meta charset="utf-8">
<title>Mirel Hatchway Photography – Business Card</title>
<link rel="stylesheet" href="https://fonts.googleapis.com/css2?family=Bebas+Neue&display=swap">
<style>
  :root {
    --paper: #fbfbfc;
    --wash-cream: #f3e2cf;
    --wash-taupe: #d9d1c2;
    --wash-edge: rgba(232, 226, 216, 0);
    --ink: #6e776b;
  }
  * { margin: 0; padding: 0; box-sizing: border-box; }
  html, body {
    width: 1200px;
    height: 678px;
    overflow: hidden;
    background: var(--paper);
  }
  .card {
    position: relative;
    width: 1200px;
    height: 678px;
    background: var(--paper);
    font-family: "Bebas Neue", "Arial Narrow", sans-serif;
    color: var(--ink);
  }
  .watercolor-wash {
    position: absolute;
    inset: 0;
    width: 1200px;
    height: 678px;
  }
  .brand {
    position: absolute;
    left: 0;
    width: 1200px;
    top: 150px;
    text-align: center;
  }
  .brand-name {
    display: block;
    font-size: 78px;
    line-height: 1;
    letter-spacing: 6px;
    font-weight: 400;
  }
  .brand-tagline {
    display: block;
    margin-top: 14px;
    font-size: 22px;
    line-height: 1;
    letter-spacing: 12px;
    font-weight: 400;
    padding-left: 12px;
  }
  .contact {
    position: absolute;
    left: 0;
    width: 1180px;
    top: 372px;
    list-style: none;
    text-align: center;
  }
  .contact-item {
    font-size: 21px;
    line-height: 1;
    letter-spacing: 0.2px;
    margin-bottom: 29px;
  }
</style>
</head>
<body>
  <main class="card">
    <svg class="watercolor-wash" viewBox="0 0 1200 678" role="img" aria-label="Soft cream and taupe watercolor wash behind the name and contact details">
      <defs>
        <radialGradient id="wash-gradient" cx="0.5" cy="0.5" r="0.5">
          <stop offset="0" stop-color="var(--wash-cream)"/>
          <stop offset="0.45" stop-color="#efe3d4"/>
          <stop offset="0.75" stop-color="var(--wash-taupe)"/>
          <stop offset="1" stop-color="#eceae5" stop-opacity="0"/>
        </radialGradient>
      </defs>
      <path fill="url(#wash-gradient)" d="M170 170 C230 90 420 40 610 40 C780 30 960 50 1030 120 C1110 200 1100 330 1080 420 C1060 520 950 590 780 610 C620 640 440 650 300 590 C170 540 120 440 140 330 C150 260 140 210 170 170 Z"/>
    </svg>

    <h1 class="brand">
      <span class="brand-name">Mirel Hatchway</span>
      <span class="brand-tagline">Photography</span>
    </h1>

    <ul class="contact">
      <li class="contact-item contact-website">www.mirelhatchway.com</li>
      <li class="contact-item contact-phone">Phone: 418.629.5073</li>
      <li class="contact-item contact-email">Email: mirel@mirelhatchway.com</li>
    </ul>
  </main>
</body>
</html>
```